Quarrybend Marble & Tile Needs a Business Card

Attached you will find your logo, my photo and design guidelines for a new business card. The final design will need two separate files to create an embossed card. The cards will be printed by www.plinkprint.com (Instructions below)
Format is the Plink SQUARE card
Quarrybend Marble And Tile is a brick and mortar, retail stone and tile shop.
One the front:
Quarrybend Marble And Tile
Dorian Fesslock
Owner
24807 Hollis Verdant Blvd
Suite P & R
Charlotte, NC 28193
Cell: 704-583-7142
Web: www.QuarrybendMarbleAndTile.com
(Make each word of the domain a different or alternating color)
On the back;
Something that shows beautiful colorful tile
Follow the design guide closely please. For more information see this page that describes creating the spot gloss file: https://www.plinkprint.com/us/business-cards/design-guidelines-spot-gloss
The logo is what we would like to have raised spot glossed.
Format is the Plink SQUARE card. See attahced guidlines.

```html
<!DOCTYPE html>
<html lang="en">
<head>
<meta charset="utf-8">
<title>Quarrybend Marble &amp; Tile — Business Card</title>
<link href="https://fonts.googleapis.com/css2?family=Crimson+Text:wght@400;600&display=swap" rel="stylesheet">
<style>
  :root {
    --page: #2a2b2c;
    --card: #fcfaf6;
    --navy: #1f2d42;
    --gold: #c08a2e;
    --rust: #b24a25;
    --olive: #6b6f4a;
    --pattern: #efe8df;
    --photo-light: #e9e3dc;
    --photo-dark: #3a3f4f;
  }
  * { margin: 0; padding: 0; box-sizing: border-box; }
  html, body { width: 1200px; height: 800px; overflow: hidden; }
  body {
    background: var(--page);
    font-family: "Crimson Text", Georgia, serif;
    color: var(--navy);
    position: relative;
  }
  .card {
    position: absolute;
    top: 243px;
    width: 550px;
    height: 314px;
    background: var(--card);
    overflow: hidden;
  }
  .card--front { left: 40px; }
  .card--back { left: 610px; }

  /* front */
  .front__pattern {
    position: absolute; left: 0; top: 0; width: 90px; height: 100%;
    background: linear-gradient(180deg, var(--pattern), #f6f1ea);
  }
  .front__photo {
    position: absolute; left: 40px; top: 96px; width: 230px; height: 218px;
    background: linear-gradient(180deg, var(--photo-light) 0%, #cdb9aa 45%, var(--photo-dark) 100%);
    border-radius: 110px 110px 0 0;
  }
  .brand {
    position: absolute; right: 34px; top: 30px;
    display: flex; align-items: center; gap: 12px;
  }
  .brand__dot {
    width: 46px; height: 46px; border-radius: 50%;
    background: var(--gold);
  }
  .brand__name {
    font-size: 18px; font-weight: 600; letter-spacing: 3px;
    text-transform: uppercase; color: var(--navy); line-height: 1.15;
  }
  .person {
    position: absolute; left: 300px; top: 118px;
  }
  .person__name { font-size: 28px; font-weight: 400; line-height: 1; }
  .person__role {
    display: flex; align-items: center; gap: 6px; margin-top: 6px;
    font-size: 10px; letter-spacing: 3px; color: var(--gold);
  }
  .person__role::after {
    content: ""; width: 34px; height: 1px; background: var(--gold);
  }
  .contact {
    position: absolute; left: 296px; top: 186px;
    border-left: 1px solid var(--gold);
    padding: 4px 0 6px 12px;
    list-style: none;
    font-size: 12.5px; line-height: 1.25;
  }
  .contact li { display: flex; align-items: flex-start; gap: 10px; margin-bottom: 8px; }
  .contact li:last-child { margin-bottom: 0; }
  .icon {
    flex: none; width: 16px; height: 16px; border-radius: 50%;
    display: flex; align-items: center; justify-content: center;
  }
  .icon--pin { background: var(--navy); }
  .icon--phone { background: var(--rust); }
  .icon--web { background: var(--olive); }
  .web__w1 { color: var(--navy); }
  .web__w2 { color: var(--olive); }
  .web__w3 { color: var(--gold); }
  .web__w4 { color: var(--rust); }

  /* back */
  .back__pattern {
    position: absolute; inset: 0;
    background: radial-gradient(circle at 50% 50%, #fbf8f3 0%, #f3ede4 70%, #ece3d8 100%);
  }
  .back__brand {
    position: absolute; left: 0; right: 0; top: 0; bottom: 0;
    display: flex; flex-direction: column; align-items: center; justify-content: center; gap: 14px;
  }
  .back__brand .brand__dot { width: 58px; height: 58px; }
  .back__brand .brand__name { font-size: 22px; text-align: center; }
</style>
</head>
<body>
  <section class="card card--front">
    <div class="front__pattern" role="img" aria-label="Faint geometric tile pattern strip"></div>
    <div class="front__photo" role="img" aria-label="Portrait photo of the owner"></div>
    <div class="brand">
      <span class="brand__dot"></span>
      <span class="brand__name">Quarrybend<br>Marble &amp; Tile</span>
    </div>
    <div class="person">
      <h1 class="person__name">Dorian Fesslock</h1>
      <p class="person__role">OWNER</p>
    </div>
    <ul class="contact">
      <li>
        <span class="icon icon--pin">
          <svg width="8" height="10" viewBox="0 0 8 10"><path d="M4 0a4 4 0 0 0-4 4c0 3 4 6 4 6s4-3 4-6a4 4 0 0 0-4-4zm0 5.5A1.5 1.5 0 1 1 4 2.5a1.5 1.5 0 0 1 0 3z" fill="#fff"/></svg>
        </span>
        <span>24807 Hollis Verdant Blvd<br>Suite P &amp; R<br>Charlotte, NC 28193</span>
      </li>
      <li>
        <span class="icon icon--phone">
          <svg width="9" height="9" viewBox="0 0 10 10"><path d="M2 1l2 2-1 1.2c.6 1.3 1.5 2.2 2.8 2.8L7 6l2 2-1.2 1.4C4.5 9 1 5.5.6 2.2z" fill="#fff"/></svg>
        </span>
        <span>Cell: 704-583-7142</span>
      </li>
      <li>
        <span class="icon icon--web">
          <svg width="10" height="10" viewBox="0 0 10 10" fill="none" stroke="#fff" stroke-width=".8"><circle cx="5" cy="5" r="4"/><ellipse cx="5" cy="5" rx="1.8" ry="4"/><path d="M1 5h8"/></svg>
        </span>
        <span>Web: www.<span class="web__w1">Quarrybend</span><span class="web__w2">Marble</span><span class="web__w3">And</span><span class="web__w4">Tile</span>.com</span>
      </li>
    </ul>
  </section>

  <section class="card card--back">
    <div class="back__pattern" role="img" aria-label="Soft colorful geometric tile pattern"></div>
    <div class="back__brand">
      <span class="brand__dot"></span>
      <span class="brand__name">Quarrybend<br>Marble &amp; Tile</span>
    </div>
  </section>
</body>
</html>
```